Young, dynamic furniture company needs a new business card design

We require a new business card design for our modern furniture company which supplies furniture and appliances to the property and development market.
Oakridge Interiors has become one of the leading furniture & appliance suppliers to the property market withing London. With over 10 years experience, we have increased our business to supply not only private landlords and managing agents, but also property developers, housing associations and local councils.
We offer not only a complete range of furniture which includes beds, wardrobes, dining sets and sofas, but also a high quality, full delivery and assembly service to help you with all our furnishing needs.

Target Market(s)

Private landlords, estate agents, letting agents, property management companies

Industry/Entity Type

Business

Contact Information for Business Card

Name,
Title,
Address,
Mobile,
Telephone,
Fax, Website, email address

Font styles to use
Sans Serif

Colors
3176b5
0555a3
85abd2
cfdeed

Requirements
Must have
• All the above information for each of our staff, along with our logo

```html
<!DOCTYPE html>
<html lang="en">
<head>
<meta charset="utf-8">
<title>Oakridge Interiors – Business Card</title>
<link href="https://fonts.googleapis.com/css2?family=Open+Sans:wght@400;600;700&display=swap" rel="stylesheet">
<style>
  :root {
    --brand-blue: #3d5f9c;
    --brand-navy: #2f2f52;
    --ink: #1c1c1c;
    --muted: #555;
    --paper: #ffffff;
    --backdrop: #e6e8ec;
  }
  * { box-sizing: border-box; margin: 0; padding: 0; }
  html, body {
    width: 1200px; height: 886px; overflow: hidden;
    background: var(--backdrop);
    font-family: "Open Sans", Arial, sans-serif;
  }
  .canvas {
    width: 1200px; height: 886px;
    display: flex; flex-direction: column; align-items: center; justify-content: center; gap: 56px;
  }
  .card {
    position: relative; width: 600px; height: 343px; overflow: hidden;
    background: var(--brand-blue);
    box-shadow: 0 6px 18px rgba(0,0,0,.18);
  }
  .card__panel { position: absolute; inset: 0; }
  .card__panel polygon { fill: var(--paper); }

  /* Brand lockup */
  .brand { position: absolute; display: flex; align-items: center; gap: 10px; white-space: nowrap; }
  .brand__mark { width: 20px; height: 20px; background: var(--brand-navy); flex: none; }
  .brand__name {
    font-size: 20px; font-weight: 600; color: var(--brand-navy);
    text-transform: uppercase; letter-spacing: .2px; line-height: 1;
  }
  .brand__tagline {
    position: absolute; font-size: 10px; font-weight: 600; color: var(--muted);
    text-transform: uppercase; letter-spacing: .4px; white-space: nowrap;
  }

  /* Front */
  .front .brand { left: 96px; top: 214px; }
  .front .brand__tagline { left: 126px; top: 242px; }

  .contact { position: absolute; left: 290px; top: 38px; right: 0; }
  .contact__name { font-size: 27px; font-weight: 700; color: var(--brand-blue); line-height: 1.1; text-transform: uppercase; white-space: nowrap; }
  .contact__role { font-size: 12px; font-weight: 700; color: var(--brand-navy); text-transform: uppercase; margin: 2px 0 0 80px; }
  .contact__rule { display: block; height: 1.5px; background: var(--brand-blue); margin-top: 14px; }
  .contact__address { margin: 22px 0 0 70px; font-size: 12.5px; color: var(--ink); line-height: 1.4; white-space: nowrap; }
  .contact__list { list-style: none; margin: 18px 0 0 70px; font-size: 12.5px; color: var(--ink); }
  .contact__list li { display: flex; align-items: center; gap: 7px; line-height: 1.55; white-space: nowrap; }
  .contact__list svg { width: 13px; height: 13px; fill: var(--brand-blue); flex: none; }

  /* Back */
  .back .brand { left: 150px; top: 130px; }
  .back .brand__mark { width: 26px; height: 26px; }
  .back .brand__name { font-size: 28px; }
  .back .brand__tagline { left: 190px; top: 170px; font-size: 12px; }
  .back__web {
    position: absolute; left: 26px; bottom: 18px;
    font-size: 15px; color: var(--paper); letter-spacing: .3px;
  }
</style>
</head>
<body>
<main class="canvas">

  <section class="card front" aria-label="Business card front">
    <svg class="card__panel" viewBox="0 0 600 343" preserveAspectRatio="none" aria-hidden="true">
      <polygon points="118,12 600,12 600,343 72,343 72,58"/>
    </svg>

    <div class="brand">
      <span class="brand__mark"></span>
      <span class="brand__name">Oakridge Interiors</span>
    </div>
    <p class="brand__tagline">Trade Furniture Solutions</p>

    <div class="contact">
      <h1 class="contact__name">Your Name</h1>
      <p class="contact__role">Position</p>
      <span class="contact__rule"></span>
      <p class="contact__address">PO BOX 1234, Address Line 1,<br>Address Line 2,<br>Address Line 3</p>
      <ul class="contact__list">
        <li><svg viewBox="0 0 16 16"><path d="M3 1h3l1.5 4-2 1.2a9 9 0 0 0 4.3 4.3L11 8.5l4 1.5v3a2 2 0 0 1-2 2A12 12 0 0 1 1 3a2 2 0 0 1 2-2z"/></svg>123-456-7890</li>
        <li><svg viewBox="0 0 16 16"><path d="M4 1h7v4H4zM1 6h14v6h-3v3H4v-3H1zM5 10v3h6v-3z"/></svg>123-456-7890</li>
        <li><svg viewBox="0 0 16 16"><path d="M1 3h14v10H1zM2.5 4.5 8 9l5.5-4.5v-.2h-11z"/></svg>youremail@oakridgemail.com</li>
        <li><svg viewBox="0 0 16 16"><circle cx="8" cy="8" r="7"/><path d="M1 8h14M8 1v14M3 4h10M3 12h10" stroke="#fff" stroke-width="1" fill="none"/></svg>www.website.com</li>
      </ul>
    </div>
  </section>

  <section class="card back" aria-label="Business card back">
    <svg class="card__panel" viewBox="0 0 600 343" preserveAspectRatio="none" aria-hidden="true">
      <polygon points="0,0 588,0 588,265 540,292 0,292"/>
    </svg>

    <div class="brand">
      <span class="brand__mark"></span>
      <span class="brand__name">Oakridge Interiors</span>
    </div>
    <p class="brand__tagline">Trade Furniture Solutions</p>

    <p class="back__web">www.website.com</p>
  </section>

</main>
</body>
</html>
```